Equipment Finance Specialist I work with companies who need the funds to buy their equipment

I would like a business card that stands out on the shelves. I want to be able to hand it to someone and say WOW. This card should have my logo.
You can put color into it I am very open on design and color

What my company does is we deal with dealerships that sell equipment such as Dump Trucks garbage trucks tractors trailers. Customers get referred to us and depending on their time in business we will ask for the following items

Companies that have been in business for more than two years we have a credit application program up to 250K . With this program we need the following items Credit application filled out(which is what I would like to be able for the customer to click on my website to get.) as well as three current month bank statements.

Deals over 250k we will need the following items

2 years business tax returns
2 years personal tax returns
Profit & Loss statement
Personal Financial Statement

what we do
100% FINANCING
SEASONAL PAYMENTS
LOAN BALLOON PAYMENTS
TRAC LEASING
LOW-INTEREST REFINANCING RATES
DEBT CONSOLIDATION

We specialize in creative financing solutions and offer a variety of reliable, flexible and expandable lending choices.

Target Market(s)

Trucking Companies

Industry/Entity Type

Trucking Company

Contact Information for Business Card

* $250,000 Application only Program
* Loans from $30,000 to 5,000,000
* Competitive Interest Rates

Font styles to use
Serif
Sans Serif

Colors

Designer to choose colors to be used in the design.

Requirements
Must have
• On the back of the card.
• * $250,000 Application only Program
• * Loans from $30,000 to 5,000,000
• My name, email, website. address
• * Competitive Interest Rates
• * 100% Financing
Nice to have
• I want my logo to pop on the card
• My logo is the great one I would like to use
Should not have
• I am up for your creativity as well

```html
<!DOCTYPE html>
<html lang="en">
<head>
<meta charset="utf-8">
<title>Keystone Haul Finance – Business Card</title>
<link rel="stylesheet" href="https://fonts.googleapis.com/css2?family=Source+Sans+3:wght@400;600;700;800&display=swap">
<style>
  :root {
    --backdrop: #3b3330;
    --card: #1c1c1d;
    --ink: #ffffff;
    --foil: #cfd1d3;
    --rule: #d8d8d8;
  }
  * { margin: 0; padding: 0; box-sizing: border-box; }
  html, body { width: 1200px; height: 864px; overflow: hidden; }
  body {
    background: var(--backdrop);
    font-family: "Source Sans 3", "Myriad Pro", Arial, sans-serif;
    color: var(--ink);
    position: relative;
  }
  .card {
    position: absolute;
    width: 560px;
    height: 320px;
    background: var(--card);
    top: 272px;
    box-shadow: 0 10px 24px rgba(0,0,0,.45);
  }
  .card--back { left: 27px; }
  .card--front { left: 613px; }

  /* Brand mark */
  .brand {
    display: flex;
    align-items: center;
    gap: 10px;
  }
  .brand__dot {
    width: 34px; height: 34px;
    border-radius: 50%;
    border: 3px solid currentColor;
    flex: none;
  }
  .brand__name {
    font-weight: 800;
    text-transform: uppercase;
    line-height: .95;
    letter-spacing: .5px;
  }

  /* Back of card */
  .card--back .brand {
    position: absolute;
    left: 0; right: 0; top: 62px;
    justify-content: center;
    color: var(--foil);
  }
  .card--back .brand__name { font-size: 34px; }
  .card--back .brand__dot { width: 44px; height: 44px; }
  .offer-list {
    position: absolute;
    left: 0; right: 0; top: 186px;
    text-align: center;
    font-size: 15.5px;
    line-height: 1.45;
    color: var(--ink);
  }

  /* Front of card */
  .card--front .brand {
    position: absolute;
    right: 30px; top: 44px;
    color: var(--ink);
  }
  .card--front .brand__name { font-size: 24px; text-align: right; }
  .holder {
    position: absolute;
    left: 30px; top: 38px;
  }
  .holder__name { font-size: 17px; font-weight: 700; text-transform: uppercase; letter-spacing: .3px; }
  .holder__title { font-size: 13px; text-transform: uppercase; letter-spacing: .4px; margin-top: 1px; }
  .rule {
    position: absolute;
    left: 30px; right: 30px;
    top: 96px;
    height: 1px;
    background: var(--rule);
  }
  .contact {
    position: absolute;
    left: 30px; top: 106px;
    list-style: none;
    font-size: 14.5px;
    line-height: 1.5;
  }
  .contact li { display: flex; align-items: center; gap: 10px; }
  .contact svg { width: 12px; height: 12px; flex: none; }
  .rule--bottom { top: 232px; left: 140px; }
  .address {
    position: absolute;
    right: 30px; top: 244px;
    text-align: right;
    font-size: 15px;
    line-height: 1.4;
  }
</style>
</head>
<body>

  <section class="card card--back" aria-label="Card back">
    <div class="brand">
      <span class="brand__dot"></span>
      <span class="brand__name">Keystone Haul<br>Finance</span>
    </div>
    <p class="offer-list">
      $250,000 Application only Program &#8226; Loans from $30,000 to 5,000,000<br>
      Competitive Interest Rates &#8226; 100% Financing
    </p>
  </section>

  <section class="card card--front" aria-label="Card front">
    <div class="holder">
      <p class="holder__name">Marcus Reed</p>
      <p class="holder__title">President</p>
    </div>

    <div class="brand">
      <span class="brand__dot"></span>
      <span class="brand__name">Keystone Haul<br>Finance</span>
    </div>

    <div class="rule"></div>

    <ul class="contact">
      <li>
        <svg viewBox="0 0 12 12" aria-hidden="true"><path fill="#fff" d="M2.5 1h2l1 2.6-1.3.9a6 6 0 0 0 3.3 3.3l.9-1.3 2.6 1v2c0 .8-.7 1.5-1.5 1.5A9.5 9.5 0 0 1 1 2.5C1 1.7 1.7 1 2.5 1z"/></svg>
        555 014 7788
      </li>
      <li>
        <svg viewBox="0 0 12 12" aria-hidden="true"><rect x="1" y="2.5" width="10" height="7" fill="#fff"/><path d="M1 2.5l5 4 5-4" fill="none" stroke="#1c1c1d" stroke-width="1"/></svg>
        marcus@keystonehaul.com
      </li>
      <li>
        <svg viewBox="0 0 12 12" aria-hidden="true"><circle cx="6" cy="6" r="5" fill="#fff"/><path d="M1 6h10M6 1c-2 2.5-2 7.5 0 10M6 1c2 2.5 2 7.5 0 10" fill="none" stroke="#1c1c1d" stroke-width=".8"/></svg>
        www.keystonehaul.com
      </li>
    </ul>

    <div class="rule rule--bottom"></div>

    <p class="address">
      2170 Harbor Crest Lane<br>
      Linden Hills, NY 10990
    </p>
  </section>

</body>
</html>
```